Business Cards for IT Consulting Company (Managed Service Provider)

I am looking to have some business cards printed and would like some designs. We are an IT Consulting company based in Vancouver BC. I would like a nice clean and modern look to the cards. I have uploaded all the versions of my logo so parts can be used as needed. Here is a snippit from our website homepage:

Quillbrook Networks Ltd. is an IT Solutions Partner located in Vancouver BC, Canada. We offer IT solutions and support to customers in the greater Vancouver Area. With expertise in Microsoft platforms, as well as Linux and Mac OSX and over 12 years experience in the IT industry, Quillbrook Networks is dedicated to offering our clients top quality service and products. We take pride in the solutions we offer our customers. The greatest compliment a client can give us is to recommend our services.

Quillbrook Networks Ltd. offers a wide range of IT services from onsite service to remote support and managed service solutions. This allows clients to choose the support path that best suits their company’s needs. Supporting many different sized companies from small to enterprise level over the past 12 years Quillbrook Networks has the experience and expertise needed to ensure things run smoothly. Allowing our clients to focus on doing business.

Revolutionizing the way IT services are delivered.

Quillbrook Networks is dedicated to providing our clients with IT solutions that work and grow with them for years to come. This philosophy helps save money in the long run instead of replacing equipment constantly. Far too often IT solutions are not well thought out and while possibly solving the problem at hand, require replacement due to growth or quality within a very short time frame. Quillbrook Networks takes pride in providing solutions that will last and be able to accommodate growth without the need for replacement.

Industry/Entity Type

Information Technology

Contact Information for Business Card

Quillbrook Networks Ltd.
(Employee Name)
Eml: (Employees Email Address)
Web: quillbrook.me
Ph: 604-555-0148

Font styles to use
Serif
Sans Serif

Requirements
Must have
• The Company logo and company colors.
Nice to have
• - Our tag line: "Revolutionizing IT Services" or "Revolutionizing the way IT services are delivered."
• - Also I really like the idea of nature and technology together blending which is sort of where my logo came from so integrating that somehow onto the business cards would be great.

```html
<!DOCTYPE html>
<html lang="en">
<head>
<meta charset="utf-8">
<title>Quillbrook Networks Ltd. — Business Card</title>
<link rel="stylesheet" href="https://fonts.googleapis.com/css2?family=Montserrat:wght@400;500;600;700&display=swap">
<style>
  :root {
    --page: #e9eaec;
    --card: #ffffff;
    --slate: #58595b;
    --slate-dark: #4a4b4d;
    --brand-blue: #1ba8e6;
    --ink: #4d4d4f;
    --paper-text: #ffffff;
  }
  * { box-sizing: border-box; margin: 0; padding: 0; }
  html, body { width: 1200px; height: 900px; overflow: hidden; }
  body {
    background: var(--page);
    font-family: "Montserrat", Arial, sans-serif;
    position: relative;
  }
  .card {
    position: absolute;
    left: 260px;
    width: 680px;
    height: 388px;
    background: var(--card);
    overflow: hidden;
    box-shadow: 0 6px 18px rgba(0,0,0,.18);
  }

  /* Front side */
  .card-front { top: 40px; }
  .front-brand {
    position: absolute;
    left: 0; right: 0; top: 118px;
    text-align: center;
    color: var(--brand-blue);
    font-size: 54px;
    font-weight: 600;
    letter-spacing: 1px;
  }
  .front-brand .brand-square {
    display: inline-block;
    width: 34px; height: 34px;
    background: var(--brand-blue);
    margin-right: 16px;
    vertical-align: -2px;
  }
  .tagline {
    position: absolute;
    left: 238px; top: 282px;
    width: 220px;
    font-size: 16px;
    font-weight: 500;
    color: var(--ink);
    letter-spacing: 1px;
    white-space: nowrap;
  }
  .rule { position: absolute; height: 2px; background: var(--brand-blue); }
  .rule-left { left: 0; top: 308px; width: 236px; }
  .rule-right { left: 470px; top: 282px; width: 210px; }

  /* Back side */
  .card-back { top: 472px; }
  .side-band {
    position: absolute;
    left: 38px; top: 0;
    width: 62px; height: 100%;
    background: var(--slate);
  }
  .info-panel {
    position: absolute;
    left: 100px; top: 212px; right: 0; bottom: 0;
    background: var(--slate);
    border-top: 3px solid var(--brand-blue);
  }
  .back-brand {
    position: absolute;
    left: 52px; top: 70px;
    display: flex; align-items: center; gap: 20px;
  }
  .back-brand .brand-square {
    width: 62px; height: 62px;
    background: var(--brand-blue);
    border: 4px solid var(--card);
  }
  .back-brand .brand-name {
    color: var(--brand-blue);
    font-size: 32px;
    font-weight: 600;
    white-space: nowrap;
  }
  .person {
    position: absolute;
    right: 36px; top: 26px;
    text-align: right;
  }
  .person-name {
    color: var(--paper-text);
    font-size: 24px;
    font-weight: 600;
    letter-spacing: 2px;
    padding-bottom: 6px;
  }
  .person-rule {
    height: 1px; width: 380px;
    background: var(--paper-text);
    margin-left: auto;
  }
  .person-role {
    color: var(--brand-blue);
    font-size: 12px;
    font-weight: 600;
    letter-spacing: 2px;
    padding-top: 4px;
  }
  .contacts {
    position: absolute;
    left: 44px; top: 96px;
    list-style: none;
  }
  .contacts li {
    display: flex; align-items: center; gap: 10px;
    color: var(--paper-text);
    font-size: 15px;
    font-weight: 500;
    letter-spacing: .5px;
    line-height: 22px;
  }
  .contacts svg { width: 12px; height: 12px; flex: none; }
</style>
</head>
<body>

  <section class="card card-front" aria-label="Card front">
    <div class="front-brand"><span class="brand-square"></span>Quillbrook</div>
    <span class="rule rule-left"></span>
    <p class="tagline">Revolutionizing IT Services</p>
    <span class="rule rule-right"></span>
  </section>

  <section class="card card-back" aria-label="Card back">
    <div class="side-band"></div>
    <div class="back-brand">
      <span class="brand-square"></span>
      <span class="brand-name">Quillbrook Networks Ltd.</span>
    </div>
    <div class="info-panel">
      <div class="person">
        <p class="person-name">MARCUS ELLERY</p>
        <div class="person-rule"></div>
        <p class="person-role">DIRECTOR</p>
      </div>
      <ul class="contacts">
        <li>
          <svg viewBox="0 0 12 12" aria-hidden="true"><path d="M2.5 1h2l1 3-1.3 1a6 6 0 0 0 2.8 2.8l1-1.3 3 1v2a1 1 0 0 1-1 1A9.5 9.5 0 0 1 1.5 2a1 1 0 0 1 1-1z" fill="#1ba8e6"/></svg>
          604-555-0148
        </li>
        <li>
          <svg viewBox="0 0 12 12" aria-hidden="true"><rect x="1" y="2.5" width="10" height="7" fill="none" stroke="#1ba8e6" stroke-width="1.2"/><path d="M1 3l5 3.5L11 3" fill="none" stroke="#1ba8e6" stroke-width="1.2"/></svg>
          info@marcusellery.com
        </li>
        <li>
          <svg viewBox="0 0 12 12" aria-hidden="true"><circle cx="6" cy="6" r="5" fill="none" stroke="#1ba8e6" stroke-width="1.2"/><ellipse cx="6" cy="6" rx="2" ry="5" fill="none" stroke="#1ba8e6" stroke-width="1"/><path d="M1 6h10" stroke="#1ba8e6" stroke-width="1"/></svg>
          www.quillbrook.me
        </li>
      </ul>
    </div>
  </section>

</body>
</html>
```